light box menu and wall graphics

HI My name is Derek Halloway and I am putting together a Pebble Mugs franchise. We are a high quaulity coffee offering and the retail concept is for a in-line store in a busy shopping centre food court. We are a highly visible coffee offering with vibrant bright orange colour (pantone 021 / process m60_y100)
Orange might make a good background on the menu board as it needs to blend in with colour scheme. Also the text has to be at least 15ml and not too busy but clearly legible. The font is: Akzent Rounded
The twin light boxes being used is from http://www.brightpanelstore.example.au/pg/lightboxes/new/sdb/light-box-1560S.aspx
They measure in total 3m wide X .6 height

There are two elements to this job, one is the twin menu boards and the other is the wall graphic.
please see wall graphic examples attached.
This graphic is to be painted onto the wall by a sign writter.
The design to go on the wall needs to be a synonymous with our quality coffee vison and match the shop design, I have examples of the type of wall art I am after attached. I was thinking somehow a Cart with wings would look neat and we could incorportate some text into it. Such as "Coffee with Substance makes you feel good" and "Original Cart" Flames could look amazing too!

My website is unfortunately down at the moment but I am attaching plenty

I have just added the menu in easy to read updated format.
Thanks to those who have expressed interest!
Updates

Hi Designers, I have just increased first prize by $100.00

Please note the signage boards run horizontally not vertically.  I have also added more artwork.

thanks

Derek

 HI there, thanks for joining.  I have just updated the brief to make it as clear as possible.

Hope you enjoy this experience.  I am here to answer any questions.

Derek

Thank you for accepting my invitation for this design job.

Look forward to seeing some designs as per brief.

Need to have this finished by Friday the 19th of October.  Thanks

Target Market(s)

Coffee lovers, kids who want hot chocolates, frappes,
etc

Industry/Entity Type

Shopping

Requirements
Must have
• Must have coffee in it for clarity.
Also in the menu any images of food or drink must be photo/posters attached

```html
<!DOCTYPE html>
<html lang="en">
<head>
<meta charset="utf-8">
<title>Pebble Mugs – Menu Light Boxes</title>
<link href="https://fonts.googleapis.com/css2?family=Nunito:wght@700;800;900&display=swap" rel="stylesheet">
<style>
  :root{
    --orange:#ee7f00;
    --ink:#231f20;
    --white:#ffffff;
    --band:#b9babc;
    --bg-light:#ffffff;
    --bg-edge:#e4e5e6;
  }
  *{margin:0;padding:0;box-sizing:border-box}
  html,body{width:1200px;height:1000px;overflow:hidden}
  body{
    position:relative;
    background:radial-gradient(ellipse at 50% 40%,var(--bg-light) 45%,var(--bg-edge) 100%);
    font-family:"Nunito",Arial,sans-serif;
    font-weight:800;
    color:var(--ink);
  }
  .mount-band{position:absolute;left:0;top:343px;width:1200px;height:314px;background:var(--band)}
  .board{position:absolute;top:356px;width:573px;height:287px;background:var(--orange);overflow:hidden}
  .board--left{left:13px}
  .board--right{left:613px}
  .header-strip{position:absolute;left:0;width:100%;height:47px;background:var(--white)}
  .pos{position:absolute;white-space:nowrap}
  .section-title{color:var(--orange);font-size:22px;font-weight:800;letter-spacing:-.3px;line-height:1}
  .price-row{font-size:14px;line-height:1;color:var(--ink);font-weight:900}
  .price-row .size{font-size:15px;margin-right:2px}
  .price-row .cur{font-size:10px;margin-right:1px}
  .price-row .big{color:var(--orange);font-size:16px}
  .price-row .cents{color:var(--orange);font-size:10px;margin-right:7px}
  .shot-note{font-size:5.5px;color:var(--orange);font-weight:800}
  .menu-list{list-style:none;font-size:14.5px;line-height:20.5px;letter-spacing:-.2px}
  .extras{list-style:none;font-size:7.5px;line-height:10px;color:var(--white);font-weight:800}
  .extras li::before{content:"•";margin-right:5px}
  .extras li.plus::before{content:"+"}
  .note{font-size:5.5px;color:var(--white);font-weight:700;margin-left:3px}
  .addon{font-size:7.5px;color:var(--white);margin-left:2px}
  .white-price{color:var(--white);font-weight:900;font-size:14px}
  .white-price small{font-size:9px}
  .white-price .d{font-size:10px;color:var(--ink)}
  .brand{display:flex;align-items:center;gap:10px;font-size:31px;font-weight:900;color:var(--ink);letter-spacing:-.5px}
  .brand-square{width:18px;height:18px;background:var(--ink)}
</style>
</head>
<body>
  <div class="mount-band"></div>

  <section class="board board--left">
    <div class="header-strip" style="top:1px"></div>
    <div class="header-strip" style="top:183px;height:48px"></div>

    <h2 class="pos section-title" style="left:15px;top:19px">Coffee</h2>
    <div class="pos price-row" style="left:124px;top:20px">
      <span class="size">S</span><span class="cur">$</span><span class="big">3</span><span class="cents">.80</span>
      <span class="size">M</span><span class="cur">$</span><span class="big">4</span><span class="cents">.50</span>
      <span class="size">L</span><span class="cur">$</span><span class="big">4</span><span class="cents">.90</span>
    </div>
    <span class="pos shot-note" style="left:124px;top:35px">(1 Shot)</span>
    <span class="pos shot-note" style="left:176px;top:35px">(2 Shot)</span>
    <span class="pos shot-note" style="left:229px;top:35px">(2 Shot)</span>

    <h2 class="pos section-title" style="left:303px;top:19px">Frappes</h2>
    <div class="pos price-row" style="left:452px;top:20px">
      <span class="size">M</span><span class="cur">$</span><span class="big">5</span><span class="cents">.00</span>
      <span class="size">L</span><span class="cur">$</span><span class="big">5</span><span class="cents">.50</span>
    </div>

    <ul class="pos menu-list" style="left:15px;top:54px">
      <li>Espresso Shot</li><li>Long Black</li><li>Flat White</li><li>Latte</li><li>Cappuccino</li><li>Hot Chocolate</li>
    </ul>
    <div class="pos white-price" style="left:140px;top:56px"><span class="d">$</span> 2.90</div>
    <ul class="pos extras" style="left:140px;top:73px">
      <li>50¢</li><li>Soy</li><li>Mocha</li><li>Vienna</li><li>Decaf (fresh)</li><li>Syrups; vanilla, caramel, hazelnut</li><li>Cream</li><li>Coffee shot</li><li>White chocolate</li>
    </ul>

    <ul class="pos menu-list" style="left:303px;top:53px">
      <li>Vanilla</li><li>Hazelnut</li><li>Caramel</li><li>Chocolate</li><li>Coffee</li>
    </ul>
    <ul class="pos menu-list" style="left:417px;top:51px;line-height:18px">
      <li>Chai</li><li>Iced Chocolate<span class="note">1 scoop ice cream</span></li><li>Iced Coffee<span class="note">1 scoop ice cream</span></li>
    </ul>
    <ul class="pos extras" style="left:417px;top:108px">
      <li class="plus">50¢</li><li>Mocha</li><li>Cream</li><li>Syrups; vanilla, caramel, hazelnut</li>
    </ul>

    <h2 class="pos section-title" style="left:15px;top:199px">Fruity Frappes</h2>
    <div class="pos price-row" style="left:177px;top:200px">
      <span class="size">M</span><span class="cur">$</span><span class="big">5</span><span class="cents">.00</span>
      <span class="size">L</span><span class="cur">$</span><span class="big">5</span><span class="cents">.50</span>
    </div>
    <h2 class="pos section-title" style="left:303px;top:199px">Chai</h2>
    <div class="pos price-row" style="left:410px;top:200px">
      <span class="size">S</span><span class="cur">$</span><span class="big">3</span><span class="cents">.80</span>
      <span class="size">M</span><span class="cur">$</span><span class="big">4</span><span class="cents">.50</span>
      <span class="size">L</span><span class="cur">$</span><span class="big">4</span><span class="cents">.90</span>
    </div>

    <ul class="pos menu-list" style="left:15px;top:238px"><li>Mango</li><li>Strawberry</li></ul>
    <ul class="pos menu-list" style="left:140px;top:238px"><li>Pineapple Paradise</li><li>Banana Smoothie<span class="addon">+ 50¢</span></li></ul>
    <ul class="pos menu-list" style="left:303px;top:238px"><li>Club Cinnamon</li><li>Vanilla Honey</li></ul>
  </section>

  <section class="board board--right">
    <div class="header-strip" style="top:1px"></div>

    <h2 class="pos section-title" style="left:15px;top:19px">Tea</h2>
    <div class="pos price-row" style="left:125px;top:20px">
      <span class="size">S</span><span class="cur">$</span><span class="big">3</span><span class="cents">.80</span>
      <span class="size">M</span><span class="cur">$</span><span class="big">4</span><span class="cents">.50</span>
      <span class="size">L</span><span class="cur">$</span><span class="big">4</span><span class="cents">.90</span>
    </div>
    <h2 class="pos section-title" style="left:302px;top:19px">Kids</h2>
    <div class="pos price-row" style="left:466px;top:20px">
      <span class="size">S</span><span class="cur">$</span><span class="big">3</span><span class="cents">.00</span>
    </div>

    <ul class="pos menu-list" style="left:15px;top:54px">
      <li>English Breakfast</li><li>Chamomile Flowers</li><li>Earl Grey Lavender</li><li>Ginger Peach</li><li>Rooibos Caramel</li><li>Hindu Chai</li><li>Japanese Sencha</li><li>African Cocoa</li><li>Wild Berry</li><li>Organic Peppermint</li>
    </ul>
    <ul class="pos menu-list" style="left:302px;top:54px">
      <li>Warm Chocolate</li><li>Cool Chocolate</li><li>Babycino Mini</li><li>Babycino Grande</li>
    </ul>
    <div class="pos white-price" style="left:426px;top:97px"><span class="d">$</span>1<small>.00</small></div>
    <div class="pos white-price" style="left:426px;top:117px"><span class="d">$</span>2<small>.50</small></div>

    <div class="pos brand" style="left:338px;top:222px"><span class="brand-square"></span>Pebble Mugs</div>
  </section>
</body>
</html>
```